Denture Clinic needs a newspaper advertisement

We need a revamped newspaper advertisement for our denture clinic based in Tweed Heads, Australia. We are currently promoting a new product called Corvalin which is a virtually non breakable, flexible denture. We have an ad the newspaper designed themselves but I feel the ad gets lost on the page and isn't effective. They have used our brand colours but apparently so does everyone else in the newspaper! We would like to see an ad that shows a quality, state of the art product but something that jumps out of the page and overrides the other ads nearby. We can't use colours that stimulate fear (like blood red) or anxiety being a dentist or black.

I have also attached a copy of the one-off full page ad we ran which shows more information about the product.

The ad size is 92mm high by 129mm wide.

Target Market(s)

95% of our patients are 65+ years old

Industry/Entity Type

Clinic

Requirements
Must have
• Must show the denture, our name, logo and details and state it is virtually unbreakable and flexible.
Should not have
• Colours that evoke fear, anxiety, trepidation.

```html
<!DOCTYPE html>
<html lang="en">
<head>
<meta charset="utf-8">
<title>Harbourline Denture Clinic – Corvalin Flexible Dentures</title>
<link rel="stylesheet" href="https://fonts.googleapis.com/css2?family=Jost:wght@400;500;600&display=swap">
<style>
  :root {
    --navy: #0c2f5c;
    --orange: #f0592a;
    --white: #ffffff;
    --ink: #1f1f1f;
    --photo-warm: #cdb59e;
    --photo-light: #ece2d7;
    --denture-pink: #e5a9a0;
  }
  * { margin: 0; padding: 0; box-sizing: border-box; }
  html, body { width: 1200px; height: 856px; overflow: hidden; background: var(--white); }
  body { font-family: "Jost", sans-serif; }
  .ad { position: relative; width: 1200px; height: 856px; background: var(--white); }
  .main-panel { position: absolute; left: 0; top: 0; width: 1200px; height: 708px; background: var(--navy); }
  .headline {
    position: absolute; left: 36px; top: 40px;
    color: var(--white); font-weight: 400; font-size: 59px; line-height: 1.36;
    letter-spacing: 0.3px; white-space: nowrap;
  }
  .couple-photo {
    position: absolute; left: 670px; top: 0; width: 530px; height: 468px;
    border-radius: 30px 0 0 30px;
    background: linear-gradient(135deg, var(--photo-light), var(--photo-warm));
  }
  .allergy-badge {
    position: absolute; left: 698px; top: 8px; width: 212px; height: 212px;
    border-radius: 50%; background: var(--orange);
    display: flex; align-items: center; justify-content: center; text-align: center;
  }
  .allergy-badge p {
    transform: rotate(-22deg);
    color: var(--white); font-weight: 600; font-size: 21px; line-height: 1.1; text-transform: uppercase;
  }
  .product-box {
    position: absolute; left: 36px; top: 322px; width: 594px; height: 344px;
    background: var(--white); border-radius: 0 22px 22px 0;
  }
  .product-intro {
    position: absolute; left: 30px; top: 22px; white-space: nowrap;
    color: var(--ink); font-size: 32px; line-height: 1.38; font-weight: 400;
  }
  .denture-photo {
    position: absolute; left: 310px; top: 158px; width: 268px; height: 174px;
    border-radius: 40px;
    background: radial-gradient(ellipse at 50% 50%, var(--denture-pink), #f3ddd6 70%, var(--white));
  }
  .footnote {
    position: absolute; left: 30px; top: 270px; width: 270px; text-align: center;
    color: var(--ink); font-size: 17px; line-height: 1.3;
  }
  .call-to-action {
    position: absolute; left: 670px; top: 508px; width: 530px; text-align: center;
    color: var(--white); font-weight: 600; font-size: 35px; line-height: 1.22;
    text-transform: uppercase;
  }
  .phone {
    position: absolute; left: 670px; top: 604px; width: 530px; text-align: center;
    color: var(--white); font-weight: 500; font-size: 60px; line-height: 1; letter-spacing: 1px;
  }
  .web-address {
    position: absolute; left: 30px; top: 740px;
    color: var(--orange); font-weight: 600; font-size: 34px; letter-spacing: 0.6px;
  }
  .practitioner {
    position: absolute; left: 30px; top: 792px;
    color: var(--ink); font-size: 26px;
  }
  .clinic-name {
    position: absolute; left: 828px; top: 738px; height: 90px;
    display: flex; align-items: center; gap: 14px;
    color: var(--navy); font-weight: 600; font-size: 30px; line-height: 1.05;
  }
  .clinic-name .mark { width: 62px; height: 62px; border-radius: 50%; background: var(--navy); flex: none; }
</style>
</head>
<body>
  <div class="ad">
    <div class="main-panel"></div>

    <h1 class="headline">WANT VIRTUALLY*<br>UNBREAKABLE,<br>FLEXIBLE DENTURES?</h1>

    <div class="couple-photo" role="img" aria-label="Smiling older couple embracing"></div>

    <div class="allergy-badge"><p>Suitable for<br>patients with<br>allergic<br>reactions!</p></div>

    <div class="product-box">
      <p class="product-intro">Introducing the Corvalin<br>denture injection system<br>by Meridex, using advanced<br>dental prosthetic<br>technology.</p>
      <div class="denture-photo" role="img" aria-label="Flexible partial denture with pink base"></div>
      <p class="footnote">*Virtually unbreakable refers to<br>the base of the denture only.</p>
    </div>

    <p class="call-to-action">Call to find something<br>to smile about!</p>
    <p class="phone">(07) 5591 2380</p>

    <p class="web-address">www.harbourlinedentures.com.au</p>
    <p class="practitioner">Daniel Ashcombe AdvDipDP Dip DT - 62 Quay Lane, Tweed Heads</p>

    <div class="clinic-name"><span class="mark"></span><span>Harbourline<br>Denture Clinic</span></div>
  </div>
</body>
</html>
```